Kestrova - presentation for a remote DBA team offering data platform management

We need a website design for wordpress site called Kestrova.cz
We deliver remote database and data platform administration and development, oversee the database administrators, consult and train the personnel responsible for the database operations. The website should include several sections, home page with graphics elements supporting the name and service - remote dba work; blog section; service introduction and description, team introduction and description, download section for documents, presentations etc.

Target Market(s)

small and medium business companies requiring remote DBA service

Number of Pages Required

3 page

Font styles to use
Sans Serif

Colors

Designer to choose colors to be used in the design.

Requirements
Must have
• The website should have several sections to introduce the services, blog, team introduction, downloads

```html
<!DOCTYPE html>
<html lang="en">
<head>
<meta charset="utf-8">
<title>Kestrova – Remote DBA Team</title>
<link href="https://fonts.googleapis.com/css2?family=Josefin+Sans:wght@400;700&family=Roboto:wght@400;500;700&display=swap" rel="stylesheet">
<style>
:root{
  --purple:#7b2d8e;
  --purple-deep:#5b3a9e;
  --blue:#1aa3e8;
  --ink:#1f1f1f;
  --text:#555;
  --muted:#888;
  --light:#f4f4f6;
  --footer:#161616;
  --white:#fff;
}
*{box-sizing:border-box;margin:0;padding:0}
html,body{width:1200px;height:3719px;overflow:hidden}
body{position:relative;font-family:Roboto,Arial,sans-serif;color:var(--text);background:var(--white)}
.abs{position:absolute}
.head{font-family:"Josefin Sans",Arial,sans-serif;font-weight:700;letter-spacing:2px}
.center{text-align:center;left:0;width:1200px}
.ghost{font-family:"Josefin Sans",Arial,sans-serif;font-weight:700;font-size:84px;letter-spacing:4px;white-space:nowrap}

/* hero */
.hero{top:0;left:0;width:1200px;height:600px;background:linear-gradient(120deg,#2b2d33 0%,#4d535c 45%,#1c1e22 100%)}
.logo{left:99px;top:38px;font-size:30px;color:var(--white)}
.nav{right:100px;top:44px;display:flex;gap:22px;font-size:14px;font-weight:500;color:var(--white);white-space:nowrap}
.hero-title{top:205px;font-size:68px;color:var(--white)}
.hero-sub{top:292px;font-size:22px;color:var(--white)}
.btn{display:flex;align-items:center;justify-content:center;gap:8px;font-size:15px;font-weight:700}
.btn-hero{left:500px;top:379px;width:199px;height:47px;background:var(--purple);color:var(--white);font-size:17px}

/* about */
.about{top:600px;left:0;width:1200px;height:520px;background:#fafafa}
.about .ghost{left:4px;top:20px;color:#ececec;font-size:80px}
.about-title{left:99px;top:86px;font-size:36px;color:var(--ink)}
.about-text{left:99px;top:158px;width:470px;font-size:13.5px;line-height:25px}
.about-text p+p{margin-top:18px}
.btn-outline{left:99px;top:374px;width:154px;height:42px;border:2px solid var(--blue);color:var(--blue);font-size:13px}
.video-frame{left:622px;top:92px;width:486px;height:327px}
.video{left:637px;top:104px;width:461px;height:302px;background:linear-gradient(135deg,#0c2a5a,#1f6fb6 60%,#9cc7e4)}

/* services */
.services{top:1120px;left:0;width:1200px;height:534px;background:linear-gradient(160deg,#6a3b9c 0%,#4f5fc0 45%,#1aa3e8 100%)}
.services .ghost{top:75px;color:rgba(255,255,255,.08)}
.sec-title{font-size:36px}
.services .sec-title{top:88px;color:var(--white)}
.services .intro{top:156px;font-size:13px;line-height:22px;color:var(--white)}
.card{top:229px;width:233px;height:218px;background:var(--white);text-align:center}
.card svg{margin-top:18px}
.card h3{margin-top:14px;font-size:14px;font-weight:700;color:var(--ink)}
.card p{margin:12px 22px 0;font-size:12px;line-height:16px;color:var(--muted)}
.arrow{font-size:26px;color:var(--white);font-weight:700}

/* insights */
.insights{top:1654px;left:0;width:1200px;height:689px;background:var(--white)}
.insights .ghost{top:60px;color:#f0f0f0}
.insights .sec-title{top:78px;color:var(--ink)}
.insights .intro{top:137px;font-size:13px;color:var(--muted)}
.post{top:193px;width:312px}
.post-img{width:312px;height:186px;position:relative}
.date{position:absolute;left:20px;top:14px;width:44px;height:58px;background:var(--purple);color:var(--white);text-align:center;font-size:11px;padding-top:8px;line-height:16px}
.date b{display:block;font-size:18px}
.date.blue{background:var(--blue)}
.post h3{margin-top:22px;font-size:19px;line-height:27px;font-weight:500;color:var(--ink)}
.meta{margin-top:10px;font-size:12px;color:var(--muted);display:flex;gap:10px;align-items:center}
.meta i{font-style:normal;color:var(--purple)}
.post p{margin-top:12px;font-size:13px;line-height:21px;color:var(--muted)}
.post .btn{margin-top:14px;width:114px;height:32px;font-size:12px}
.post .btn.outline{border:2px solid var(--blue);color:var(--blue)}
.post .btn.solid{background:var(--purple);color:var(--white)}

/* team */
.team{top:2343px;left:0;width:1200px;height:533px;background:var(--blue)}
.team .ghost{top:82px;color:rgba(255,255,255,.14)}
.team .sec-title{top:93px;color:var(--white)}
.member{top:151px;width:300px;text-align:center;color:var(--white)}
.avatar{width:158px;height:158px;border-radius:50%;border:5px solid var(--white);margin:0 auto;background:linear-gradient(160deg,#c9d3dd,#6d7c8c)}
.member h4{margin-top:32px;font-size:12px;font-weight:700}
.member h4 span{font-weight:400}
.member p{margin-top:10px;font-size:12px;line-height:19px}
.socials{margin-top:10px;display:flex;justify-content:center;gap:8px}
.dot{width:12px;height:12px;border-radius:50%;background:var(--white)}

/* clients */
.clients{top:2876px;left:0;width:1200px;height:446px;background:linear-gradient(180deg,#f7f7f8,#e9ebee)}
.clients .ghost{top:92px;color:#e4e4e6}
.clients .sec-title{top:104px;color:var(--ink)}
.clients .intro{top:152px;font-size:13px;color:var(--muted)}
.client{top:208px;height:99px;background:var(--white);display:flex;align-items:center;justify-content:center;font-size:26px;font-weight:500;color:#8a8f96}
.client.active{border:1px solid #cfd4da;color:var(--ink)}
.slider-arrow{top:240px;font-size:28px;color:#b5b5b5}
.pager{top:356px;left:565px;display:flex;gap:8px}
.pager span{width:16px;height:3px;background:#9aa0a6}
.pager span.on{background:var(--blue)}

/* footer */
.footer{top:3322px;left:0;width:1200px;height:397px;background:var(--footer);color:#ddd}
.f-social{left:99px;top:78px;display:flex;gap:20px}
.f-social .dot{width:20px;height:20px}
.f-line{left:99px;top:119px;width:72px;height:2px;background:var(--blue)}
.f-links{left:99px;top:144px;list-style:none;font-size:12.5px;line-height:21px}
.f-links li::before{content:"» ";color:#aaa}
.f-title{font-size:14px;font-weight:700;letter-spacing:1px;color:var(--white)}
.news{left:451px;top:72px;width:293px;text-align:center}
.news p{margin-top:22px;font-size:12px;line-height:20px}
.news .input{margin-top:16px;height:45px;border:2px solid var(--blue);display:flex;align-items:center;justify-content:center;font-size:12px;color:#ccc}
.news .subscribe{margin-top:17px;height:45px;background:var(--blue);color:var(--white);display:flex;align-items:center;justify-content:center;font-weight:700;font-size:15px}
.company{left:885px;top:72px;width:260px}
.info{display:flex;gap:14px;font-size:12px;line-height:20px;margin-top:22px}
.info svg{flex:none;margin-top:3px}
.info b{color:var(--white)}
.copy{top:346px;font-size:13px;font-weight:700;color:var(--white)}
</style>
</head>
<body>

<header class="abs hero" role="img" aria-label="Photo of a person working on a laptop with data chart overlays">
  <div class="abs logo head">KESTROVA</div>
  <nav class="abs nav"><span>HOME</span><span>ABOUT US</span><span>SERVICES</span><span>SOLUTION</span><span>BLOG</span><span>DOWNLOADS</span><span>CONTACT US</span></nav>
  <h1 class="abs center head hero-title">KESTROVA</h1>
  <p class="abs center hero-sub">We are a Remote DBA Team Offering Data Platform Management</p>
  <div class="abs btn btn-hero">READ MORE <span>➜</span></div>
</header>

<section class="abs about">
  <div class="abs ghost">ABOUT US</div>
  <h2 class="abs head about-title">WELCOME TO KESTROVA</h2>
  <div class="abs about-text">
    <p>At vero eos et accusamus et iusto odio dignissimos ducimus qui blanditiis praesentium voluptatum deleniti atque corrupti.</p>
    <p>Quos dolores et quas molestias excepturi sint occaecati cupiditate non provident, similique sunt in culpa qui officia deserunt mollitia animi, id est laborum et dolorum fuga. Et harum quidem rerum facilis est et expedita distinctio. Nam libero tempore cum soluta nobis.</p>
  </div>
  <div class="abs btn btn-outline">READ MORE <span>➜</span></div>
  <svg class="abs video-frame" viewBox="0 0 486 327" fill="none" stroke="#7b2d8e" stroke-width="3">
    <path d="M1 40V1H40M446 1H485V40M485 287V326H446M40 326H1V287"/>
  </svg>
  <div class="abs video" role="img" aria-label="Video still of a hand touching a laptop with cloud data graphics"></div>
  <svg class="abs" style="left:838px;top:230px" width="58" height="52" viewBox="0 0 58 52"><circle cx="29" cy="26" r="25" fill="rgba(255,255,255,.9)"/><path d="M23 15L39 26L23 37Z" fill="#1f1f1f"/></svg>
</section>

<section class="abs services">
  <div class="abs center ghost">OUR SERVICES</div>
  <h2 class="abs center head sec-title">OUR SERVICES</h2>
  <p class="abs center intro">If your database is slow or won't respond, you need our expert help fast, especially if your data is still inside<br>your business. We have experts on hand to repair your database.</p>
  <div class="abs arrow" style="left:50px;top:312px">‹</div>
  <div class="abs arrow" style="left:1132px;top:312px">›</div>

  <div class="abs card" style="left:99px">
    <svg width="64" height="64" viewBox="0 0 64 64" fill="none" stroke="#1aa3e8" stroke-width="2"><ellipse cx="32" cy="12" rx="20" ry="6"/><path d="M12 12v36c0 3 9 6 20 6s20-3 20-6V12M12 24c0 3 9 6 20 6s20-3 20-6M12 36c0 3 9 6 20 6s20-3 20-6"/></svg>
    <h3>REMOTE DATABASE</h3>
    <p>Derit in voluptate velit vera duis aute irure dolor esse repreher esse cillum dolo fugiat nulla</p>
  </div>
  <div class="abs card" style="left:357px">
    <svg width="64" height="64" viewBox="0 0 64 64" fill="none" stroke="#5b3a9e" stroke-width="2"><rect x="8" y="8" width="34" height="26"/><rect x="22" y="26" width="34" height="26" stroke="#1aa3e8"/><path d="M14 16h20M14 22h14M28 34h20M28 40h14"/></svg>
    <h3>DBA &amp; DEVELOPMENT</h3>
    <p>Derit in voluptate velit vera duis aute irure dolor esse repreher esse cillum dolo fugiat nulla</p>
  </div>
  <div class="abs card" style="left:612px">
    <svg width="64" height="64" viewBox="0 0 64 64" fill="none" stroke="#1aa3e8" stroke-width="2"><rect x="24" y="6" width="16" height="14"/><rect x="6" y="40" width="16" height="14"/><rect x="42" y="40" width="16" height="14" stroke="#5b3a9e"/><path d="M32 20v10M14 40V30h36v10"/></svg>
    <h3>OVERSEE THE DBA</h3>
    <p>Derit in voluptate velit vera duis aute irure dolor esse repreher esse cillum dolo fugiat nulla</p>
  </div>
  <div class="abs card" style="left:868px">
    <svg width="64" height="64" viewBox="0 0 64 64" fill="none" stroke="#5b3a9e" stroke-width="2"><circle cx="20" cy="24" r="8"/><circle cx="44" cy="24" r="8" stroke="#1aa3e8"/><path d="M6 54c0-10 6-16 14-16s14 6 14 16M30 54c0-10 6-16 14-16s14 6 14 16"/><path d="M26 6h12v8H26z" stroke="#1aa3e8"/></svg>
    <h3>CONSULTING &amp; TRAINING</h3>
    <p>Derit in voluptate velit vera duis aute irure dolor esse repreher esse cillum dolo fugiat nulla</p>
  </div>
</section>

<section class="abs insights">
  <div class="abs center ghost">OUR INSIGHTS</div>
  <h2 class="abs center head sec-title">OUR INSIGHTS</h2>
  <p class="abs center intro">Lorem ipsum dolor sit amet, consectetur adipiscing elit sed do eiusmod.</p>

  <article class="abs post" style="left:99px">
    <div class="post-img" role="img" aria-label="Tablet showing a data management graphic on a desk" style="background:linear-gradient(135deg,#d9dfe5,#6f8aa3 60%,#2f4a66)"><div class="date">Aug<b>12</b></div></div>
    <h3>Minus id quod maxime placeat Facere possimus</h3>
    <div class="meta"><i>●</i>Erik Salm <span>|</span><i style="color:#1aa3e8">●</i>214 Comments</div>
    <p>Nam libero tempore, cum soluta nobis est eligendi optio cumque nihil impedit quo minus</p>
    <div class="btn outline">Read More <span>➜</span></div>
  </article>
  <article class="abs post" style="left:444px">
    <div class="post-img" role="img" aria-label="Person working at monitors full of code" style="background:linear-gradient(135deg,#3a4450,#1c232b 60%,#59718a)"><div class="date blue">Aug<b>18</b></div></div>
    <h3>Minus id quod maxime placeat Facere possimus</h3>
    <div class="meta"><i>●</i>Erik Salm <span>|</span><i style="color:#1aa3e8">●</i>214 Comments</div>
    <p>Nam libero tempore, cum soluta nobis est eligendi optio cumque nihil impedit quo minus</p>
    <div class="btn solid">Read More <span>➜</span></div>
  </article>
  <article class="abs post" style="left:786px">
    <div class="post-img" role="img" aria-label="Engineers standing in a server room" style="background:linear-gradient(135deg,#1b2c4f,#2f5c9a 55%,#0f1a33)"><div class="date">Aug<b>28</b></div></div>
    <h3>Minus id quod maxime placeat Facere possimus</h3>
    <div class="meta"><i>●</i>Erik Salm <span>|</span><i style="color:#1aa3e8">●</i>214 Comments</div>
    <p>Nam libero tempore, cum soluta nobis est eligendi optio cumque nihil impedit quo minus</p>
    <div class="btn outline">Read More <span>➜</span></div>
  </article>
</section>

<section class="abs team">
  <div class="abs center ghost">OUR TEAM</div>
  <h2 class="abs center head sec-title">OUR TEAM</h2>
  <div class="abs member" style="left:86px">
    <div class="avatar" role="img" aria-label="Portrait photo of team member Marek Vold"></div>
    <h4>MAREK VOLD, <span>Co Founder</span></h4>
    <p>Nam libero tempore, cum soluta nobis eligendi quia<br>numquam quod maxue place facere</p>
    <div class="socials"><span class="dot"></span><span class="dot"></span><span class="dot"></span></div>
  </div>
  <div class="abs member" style="left:450px">
    <div class="avatar" role="img" aria-label="Portrait photo of team member Ilona Brest"></div>
    <h4>ILONA BREST, <span>CEO &amp; Co Founder</span></h4>
    <p>Nam libero tempore, cum soluta nobis eligendi quia<br>numquam quod maxue place facere</p>
    <div class="socials"><span class="dot"></span><span class="dot"></span><span class="dot"></span></div>
  </div>
  <div class="abs member" style="left:814px">
    <div class="avatar" role="img" aria-label="Portrait photo of team member Tomas Rall"></div>
    <h4>TOMAS RALL, <span>Co Founder</span></h4>
    <p>Nam libero tempore, cum soluta nobis eligendi quia<br>numquam quod maxue place facere</p>
    <div class="socials"><span class="dot"></span><span class="dot"></span><span class="dot"></span></div>
  </div>
</section>

<section class="abs clients">
  <div class="abs center ghost">OUR CLIENTS</div>
  <h2 class="abs center head sec-title">OUR CLIENTS</h2>
  <p class="abs center intro">Clients we are proud to have worked with us</p>
  <div class="abs slider-arrow" style="left:98px">‹</div>
  <div class="abs slider-arrow" style="left:1090px">›</div>
  <div class="abs client" style="left:156px;width:179px">Fizzora</div>
  <div class="abs client" style="left:394px;width:176px">Lensio</div>
  <div class="abs client active" style="left:620px;width:198px">Wayfen</div>
  <div class="abs client" style="left:868px;width:173px">Norvik</div>
  <div class="abs pager"><span></span><span></span><span class="on"></span><span></span></div>
</section>

<footer class="abs footer">
  <div class="abs f-social"><span class="dot"></span><span class="dot"></span><span class="dot"></span><span class="dot"></span><span class="dot"></span></div>
  <div class="abs f-line"></div>
  <ul class="abs f-links"><li>Home</li><li>About Us</li><li>Our Services</li><li>Blog</li><li>Solutions</li><li>Downloads</li><li>Contact Us</li></ul>

  <div class="abs news">
    <h4 class="f-title">NEWSLETTER SUBSCRIPTION</h4>
    <p>Register your Email Address to get a more<br>Information about us</p>
    <div class="input">Email Address *</div>
    <div class="subscribe">SUBSCRIBE</div>
  </div>

  <div class="abs company">
    <h4 class="f-title">COMPANY INFORMATION</h4>
    <div class="info"><svg width="12" height="16" viewBox="0 0 12 16"><path d="M6 0a6 6 0 0 0-6 6c0 4 6 10 6 10s6-6 6-10a6 6 0 0 0-6-6zm0 8.5A2.5 2.5 0 1 1 6 3.5a2.5 2.5 0 0 1 0 5z" fill="#fff"/></svg><div><b>Kestrova</b><br>48 Lindova Street, Brnovice<br>Central District, CZ</div></div>
    <div class="info"><svg width="14" height="14" viewBox="0 0 14 14"><path d="M3 0l3 3-2 2c1 2 3 4 5 5l2-2 3 3-2 3C6 14 0 8 0 2z" fill="#fff"/></svg><div>(+420) 555 018 244</div></div>
    <div class="info"><svg width="14" height="11" viewBox="0 0 14 11"><rect width="14" height="11" fill="#fff"/><path d="M0 0l7 6 7-6" stroke="#161616" fill="none"/></svg><div>sales@kestrova.cz</div></div>
  </div>

  <p class="abs center copy">Copyrights © 2018 Kestrova. All Rights Reserved &nbsp; | &nbsp; Privacy Policy.</p>
</footer>

</body>
</html>
```